Flat bootstrap design for existing site

I'm looking for a modern flat design based around an existing logo. This has to be a custom design (no external templates), and implemented into a bootstrap framework.

The logo is attached as 2 versions - choose whichever you want, that flows better with whatever design you choose.

Added screenshots of the existing site (currently using the default bootstrap layouts). Please make your designs around those pages in the screenshots (i.e. the homepage only has the postal code input and the header). The active page has 3 screenshots, because I wanted to illustrate the other states that would be visible (in the table rows).

This is a moving/junk removal website, just for some context.

Here's some example websites (flat designs) that I like, just to give you an idea of what I'm after.

https://www.plimvora.com/
https://dacklow.com/
https://trevanu.com/
https://quobrintal.com/en/

Coding

Coded - Design and coding required

Number of Pages Required

5+ page

Colors

Designer to choose colors to be used in the design.

Requirements
Must have
• It must be a modern/simple flat design, that is built around the existing logo (attached).
• It has to be implemented using bootstrap.

```html
<!DOCTYPE html>
<html lang="en">
<head>
<meta charset="utf-8">
<title>Torvane · Sign In</title>
<link rel="stylesheet" href="https://fonts.googleapis.com/css2?family=Raleway:wght@400;500;700&family=Open+Sans:wght@400;600;700&display=swap">
<style>
  :root {
    --accent: #4cc8f4;
    --white: #ffffff;
    --field-text: #8a8a8a;
    --field-icon: #7a7a7a;
    --rule: rgba(255, 255, 255, 0.55);
    --sky: #3a4a58;
    --trees: #3b4236;
    --grass: #4a4a2e;
    --road: #2e302c;
  }

  * { box-sizing: border-box; margin: 0; padding: 0; }

  html, body {
    width: 1200px;
    height: 666px;
    overflow: hidden;
  }

  body {
    font-family: "Open Sans", Arial, sans-serif;
    color: var(--white);
    background: var(--road);
  }

  .page {
    position: relative;
    width: 1200px;
    height: 666px;
    overflow: hidden;
  }

  .hero-photo {
    position: absolute;
    inset: 0;
    background:
      linear-gradient(180deg, rgba(20, 28, 36, 0.35) 0%, rgba(20, 24, 22, 0.45) 100%),
      linear-gradient(180deg, var(--sky) 0%, #46504a 35%, var(--trees) 62%, var(--grass) 84%, var(--road) 100%);
  }

  .site-header {
    position: absolute;
    top: 0;
    left: 0;
    width: 1200px;
    height: 107px;
    border-bottom: 1px solid var(--rule);
  }

  .brand {
    position: absolute;
    left: 99px;
    top: 32px;
    display: flex;
    align-items: center;
    gap: 10px;
    font-family: "Raleway", Arial, sans-serif;
    font-weight: 700;
    font-size: 36px;
    letter-spacing: 1px;
    color: var(--white);
  }

  .brand-dot {
    width: 14px;
    height: 14px;
    border-radius: 50%;
    background: var(--white);
  }

  .main-nav {
    position: absolute;
    top: 36px;
    right: 86px;
    display: flex;
    align-items: center;
    gap: 18px;
  }

  .nav-link {
    display: block;
    padding: 0 9px;
    height: 34px;
    line-height: 34px;
    font-family: "Raleway", Arial, sans-serif;
    font-weight: 500;
    font-size: 16px;
    color: var(--white);
    text-decoration: none;
  }

  .nav-link--highlight {
    background: var(--accent);
    padding: 0 10px;
  }

  .signin {
    position: absolute;
    top: 236px;
    left: 0;
    width: 1200px;
    text-align: center;
  }

  .signin-title {
    font-family: "Raleway", Arial, sans-serif;
    font-weight: 400;
    font-size: 50px;
    line-height: 60px;
    letter-spacing: 0.5px;
    text-shadow: 0 1px 3px rgba(0, 0, 0, 0.35);
  }

  .signin-title strong {
    font-family: "Open Sans", Arial, sans-serif;
    font-weight: 700;
  }

  .signin-form {
    width: 451px;
    margin: 28px auto 0;
  }

  .field {
    display: flex;
    align-items: center;
    gap: 8px;
    height: 50px;
    padding: 0 22px;
    background: var(--white);
    margin-bottom: 17px;
  }

  .field svg { flex: none; fill: var(--field-icon); }

  .field input {
    border: 0;
    outline: 0;
    flex: 1;
    font-family: "Open Sans", Arial, sans-serif;
    font-size: 15px;
    color: #333;
    background: transparent;
  }

  .field input::placeholder { color: var(--field-text); }

  .login-button {
    display: block;
    width: 136px;
    height: 49px;
    margin: 3px auto 0;
    border: 0;
    border-radius: 25px;
    background: var(--accent);
    color: var(--white);
    font-family: "Open Sans", Arial, sans-serif;
    font-weight: 700;
    font-size: 16px;
    letter-spacing: 0.5px;
  }

  .site-footer {
    position: absolute;
    top: 613px;
    left: 0;
    width: 1200px;
    text-align: center;
    font-size: 12px;
  }
</style>
</head>
<body>
  <div class="page">
    <div class="hero-photo" role="img" aria-label="Photo of a green roll-off dumpster truck driving along a road lined with bare trees and grass, darkened"></div>

    <header class="site-header">
      <div class="brand"><span class="brand-dot"></span>TORVANE</div>
      <nav class="main-nav">
        <a class="nav-link" href="#">Book</a>
        <a class="nav-link" href="#">How it Works</a>
        <a class="nav-link nav-link--highlight" href="#">Become a Driver</a>
        <a class="nav-link" href="#">Sign In</a>
      </nav>
    </header>

    <main class="signin">
      <h1 class="signin-title">PLEASE <strong>SIGN IN</strong></h1>
      <form class="signin-form">
        <label class="field">
          <svg width="15" height="11" viewBox="0 0 15 11" aria-hidden="true"><path d="M0 0h15v1.6L7.5 6 0 1.6z"/><path d="M0 3.2l7.5 4.4L15 3.2V11H0z"/></svg>
          <input type="email" placeholder="Email Address">
        </label>
        <label class="field">
          <svg width="11" height="13" viewBox="0 0 11 13" aria-hidden="true"><path d="M2 5V3.5a3.5 3.5 0 0 1 7 0V5h-1.6V3.5a1.9 1.9 0 0 0-3.8 0V5z"/><rect x="0" y="5" width="11" height="8" rx="1"/></svg>
          <input type="password" placeholder="Password">
        </label>
        <button class="login-button" type="button">LOGIN</button>
      </form>
    </main>

    <footer class="site-footer">Copyrights © 2017, Torvane . All Rights Reserved.</footer>
  </div>
</body>
</html>
```